Business Card Design for Occupational Medicine Start Up Company

We need to design a professional business card. We are a healthcare company providing occupational medicine services to blue collar industries. We are professional, efficient and high quality service providers.

Target Market(s)

Blue Collar Industry: Shipbuilding, Ports, Trucking Companies; The Executives and Safety Officers for these companies

Industry/Entity Type

Healthcare

Contact Information for Business Card

Logo, Name, Title, Email, Phone

Other font styles liked:
• Please match our Brand Guide

Requirements
Must have
• Our Company Colors and Logo

```html
<!DOCTYPE html>
<html lang="en">
<head>
<meta charset="UTF-8">
<title>CrewWell Clinics – Business Card</title>
<link href="https://fonts.googleapis.com/css2?family=Montserrat:wght@500;600;700&display=swap" rel="stylesheet">
<style>
  :root {
    --backdrop: #2b2b2b;
    --navy: #2f2d74;
    --sky: #2b9ad6;
    --gold: #e8a93a;
    --paper: #f4f4f4;
    --white: #ffffff;
  }
  * { box-sizing: border-box; margin: 0; padding: 0; }
  html, body { width: 1200px; height: 1200px; overflow: hidden; }
  body {
    background: var(--backdrop);
    font-family: "Montserrat", sans-serif;
    position: relative;
  }
  .card {
    position: absolute;
    width: 594px;
    height: 350px;
    border-radius: 22px;
    overflow: hidden;
  }
  /* Front */
  .card-front {
    left: 298px; top: 198px;
    background: var(--navy);
    color: var(--white);
  }
  .front-brand {
    position: absolute;
    top: 96px; left: 0; right: 0;
    display: flex; flex-direction: column; align-items: center; gap: 18px;
  }
  .brand-dot {
    width: 58px; height: 58px; border-radius: 50%;
    background: var(--sky);
  }
  .brand-name {
    font-weight: 600;
    font-size: 34px;
    letter-spacing: 1px;
    text-transform: uppercase;
    line-height: 1;
  }
  .front-brand .brand-name { color: var(--white); }
  .front-url {
    position: absolute;
    bottom: 28px; left: 0; right: 0;
    text-align: center;
    font-size: 16px; font-weight: 500; letter-spacing: 1px;
  }
  .front-url .accent { color: var(--sky); }

  /* Back */
  .card-back {
    left: 292px; top: 636px;
    background: var(--paper);
    color: var(--navy);
  }
  .back-brand {
    position: absolute;
    left: 40px; top: 108px;
    width: 230px;
    display: flex; flex-direction: column; align-items: center; gap: 16px;
  }
  .back-brand .brand-dot { width: 50px; height: 50px; background: var(--navy); }
  .back-brand .brand-name { color: var(--navy); font-size: 24px; text-align: center; line-height: 1.2; }
  .contact {
    position: absolute;
    left: 316px; top: 66px;
  }
  .person-name {
    color: var(--sky);
    font-weight: 600; font-size: 23px; letter-spacing: 0.5px;
    text-transform: uppercase; line-height: 1.1;
  }
  .person-title { font-size: 15px; font-weight: 500; margin-top: 2px; }
  .contact-list { list-style: none; margin-top: 22px; }
  .contact-list li {
    display: flex; align-items: center; gap: 12px;
    font-size: 15px; font-weight: 500; line-height: 21px;
  }
  .contact-list svg { width: 15px; height: 15px; flex: none; }
  .address { margin-top: 18px; display: flex; gap: 12px; font-size: 15px; font-weight: 500; line-height: 21px; }
  .address svg { width: 15px; height: 15px; margin-top: 3px; flex: none; }
  .stripes { position: absolute; left: 0; bottom: 0; width: 594px; height: 44px; }
  .specialty {
    position: absolute; right: 0; bottom: 0;
    width: 320px; height: 42px;
    display: flex; align-items: center; justify-content: center;
    padding-left: 20px;
    color: var(--white); font-size: 15px; font-weight: 500;
  }
</style>
</head>
<body>
  <section class="card card-front">
    <div class="front-brand">
      <div class="brand-dot"></div>
      <div class="brand-name">CrewWell Clinics</div>
    </div>
    <div class="front-url">www.<span class="accent">crewwellclinics</span>.com</div>
  </section>

  <section class="card card-back">
    <div class="back-brand">
      <div class="brand-dot"></div>
      <div class="brand-name">CrewWell Clinics</div>
    </div>

    <div class="contact">
      <div class="person-name">Dana Reyes</div>
      <div class="person-title">Senior Doctor</div>
      <ul class="contact-list">
        <li>
          <svg viewBox="0 0 16 16" aria-hidden="true"><path fill="var(--sky)" d="M3 2h3l1.5 3.5-2 1.2a8 8 0 0 0 3.8 3.8l1.2-2L14 10v3a1 1 0 0 1-1 1A11 11 0 0 1 2 3a1 1 0 0 1 1-1z"/></svg>
          555-014-2288
        </li>
        <li>
          <svg viewBox="0 0 16 16" aria-hidden="true"><rect x="1" y="3" width="14" height="10" rx="1" fill="var(--navy)"/><path d="M1.5 3.8 8 9l6.5-5.2" fill="none" stroke="var(--paper)" stroke-width="1.3"/></svg>
          dana@crewwellclinics.com
        </li>
        <li>
          <svg viewBox="0 0 16 16" aria-hidden="true"><g fill="none" stroke="var(--gold)" stroke-width="1.3"><circle cx="8" cy="8" r="6.5"/><ellipse cx="8" cy="8" rx="3" ry="6.5"/><path d="M1.5 8h13M2.5 4.8h11M2.5 11.2h11"/></g></svg>
          www.crewwellclinics.com
        </li>
      </ul>
      <div class="address">
        <svg viewBox="0 0 16 16" aria-hidden="true"><path fill="var(--gold)" d="M8 1a5 5 0 0 1 5 5c0 3.6-5 9-5 9S3 9.6 3 6a5 5 0 0 1 5-5zm0 3a2 2 0 1 0 0 4 2 2 0 0 0 0-4z"/></svg>
        <span>48 Harbor Lane, Suite 210<br>Bayside, State 40210</span>
      </div>
    </div>

    <svg class="stripes" viewBox="0 0 594 44" aria-hidden="true">
      <rect x="0" y="17" width="300" height="5" fill="var(--sky)"/>
      <rect x="0" y="27" width="300" height="5" fill="var(--navy)"/>
      <rect x="0" y="37" width="300" height="5" fill="var(--gold)"/>
      <path d="M290 44 L308 4 Q310 2 314 2 H594 V44 Z" fill="var(--navy)"/>
    </svg>
    <div class="specialty">Occupational Medicine</div>
  </section>
</body>
</html>
```